Baby Boutique Needs a Business Card Design

We need a modern double sided business card design using the attached logo for Little Wren Nook.

Little Wren Nook is a baby boutique which sells only handmade clothing and accessories for both boys and girls. Our store will live exclusively online.

We would like to only use the colors that have been used in the logo.

Target Market(s)

Potential wholesale clients, Small business owners

Industry/Entity Type

Retail

Contact Information for Business Card

Name Gideon R. Falkner (Owner)
Email sales@littlewrennook.example
Main Phone 555-203-7719
Cell phone 555-203-7746
Website www.LittleWrenNook.example

Font styles to use
Sans Serif

Colors

Designer to choose colors to be used in the design.

Requirements
Must have
• -Would like to have icons that indentify the contact information.
• -Include our website
• -Include our tagline in a small area near the bottom. "Handmade Baby Creations"
• -Would like to include Facebook and Instagram Icons
• -
Nice to have
• Would like to have a simple back side with the logo.
• Something along the lines of the meadowfield lending card attached.

```html
<!DOCTYPE html>
<html lang="en">
<head>
<meta charset="utf-8">
<title>Little Wren Nook – Business Card</title>
<link href="https://fonts.googleapis.com/css2?family=Work+Sans:wght@400;500;600&display=swap" rel="stylesheet">
<style>
  :root {
    --backdrop: #3a322e;
    --card-black: #1b1b1c;
    --card-back: #19191a;
    --teal: #74d3bf;
    --coral: #e8605f;
    --grey: #9a9a9a;
    --emboss: #3a3a3c;
  }
  * { box-sizing: border-box; margin: 0; padding: 0; }
  html, body { width: 1200px; height: 715px; overflow: hidden; }
  body {
    background: var(--backdrop);
    font-family: "Work Sans", Arial, sans-serif;
    position: relative;
  }
  .card {
    position: absolute;
    top: 203px;
    width: 540px;
    height: 309px;
    border-radius: 4px;
    overflow: hidden;
  }
  /* Back side */
  .card-back {
    left: 30px;
    background: var(--card-back);
    border-bottom: 4px solid var(--teal);
    display: flex;
    align-items: center;
    justify-content: center;
  }
  .back-brand {
    display: flex;
    align-items: center;
    gap: 12px;
    color: var(--emboss);
    font-weight: 600;
    font-size: 34px;
  }
  .brand-dot {
    width: 14px; height: 14px; border-radius: 50%;
    background: currentColor;
  }
  /* Front side */
  .card-front {
    left: 630px;
    background: var(--card-black);
  }
  .front-brand {
    position: absolute;
    left: 0; top: 0;
    width: 260px; height: 262px;
    display: flex; align-items: center; justify-content: center;
    gap: 10px;
    color: var(--teal);
    font-weight: 600;
    font-size: 26px;
  }
  .front-brand .brand-dot { background: var(--coral); width: 10px; height: 10px; }
  .divider {
    position: absolute;
    left: 262px; top: 58px;
    width: 2px; height: 204px;
    background: var(--teal);
  }
  .contact {
    position: absolute;
    left: 286px; top: 70px;
    width: 240px;
  }
  .contact-name {
    color: var(--coral);
    font-weight: 600;
    font-size: 19px;
    letter-spacing: 0.2px;
  }
  .contact-role {
    color: var(--grey);
    font-size: 11px;
    margin-top: 2px;
    margin-bottom: 14px;
  }
  .contact-list { list-style: none; }
  .contact-list li {
    display: flex; align-items: center; gap: 8px;
    color: var(--teal);
    font-size: 12.5px;
    line-height: 19px;
    white-space: nowrap;
  }
  .contact-list svg { width: 9px; height: 9px; flex: none; }
  .social {
    position: absolute;
    right: 46px; bottom: 62px;
    display: flex; gap: 10px;
  }
  .social-slot {
    width: 18px; height: 18px;
    border-radius: 3px;
    background: var(--coral);
  }
  .rule {
    position: absolute;
    left: 0; right: 0; bottom: 38px;
    height: 2px;
    background: var(--teal);
  }
  .tagline-band {
    position: absolute;
    left: 0; right: 0; bottom: 0;
    height: 36px;
    background: var(--coral);
  }
  .tagline {
    position: absolute;
    left: 0; bottom: 0;
    width: 262px; height: 36px;
    display: flex; align-items: center; justify-content: center;
    color: #f4dede;
    font-size: 12px;
    letter-spacing: 0.6px;
  }
</style>
</head>
<body>
  <section class="card card-back" aria-label="Card back">
    <div class="back-brand"><span class="brand-dot"></span>Little Wren Nook</div>
  </section>

  <section class="card card-front" aria-label="Card front">
    <div class="front-brand"><span class="brand-dot"></span>Little Wren Nook</div>
    <div class="divider"></div>

    <div class="contact">
      <p class="contact-name">Gideon R. Falkner</p>
      <p class="contact-role">Owner</p>
      <ul class="contact-list">
        <li>
          <svg viewBox="0 0 10 10"><path d="M2 1l2 2-1 1.2c.6 1.2 1.5 2.1 2.8 2.8L7 6l2 2-1.3 1.3C4.5 9 1 5.5.7 2.3z" fill="#e8605f"/></svg>
          555-203-7719
        </li>
        <li>
          <svg viewBox="0 0 10 10"><rect x="2.5" y="0.5" width="5" height="9" rx="1" fill="none" stroke="#e8605f"/><circle cx="5" cy="8" r=".6" fill="#e8605f"/></svg>
          555-203-7746
        </li>
        <li>
          <svg viewBox="0 0 10 10"><rect x=".5" y="2" width="9" height="6" fill="none" stroke="#e8605f"/><path d="M.5 2l4.5 3.5L9.5 2" fill="none" stroke="#e8605f"/></svg>
          sales@littlewrennook.example
        </li>
        <li>
          <svg viewBox="0 0 10 10"><circle cx="5" cy="5" r="4.5" fill="none" stroke="#e8605f"/><path d="M.5 5h9M5 .5c-2.4 2.7-2.4 6.3 0 9M5 .5c2.4 2.7 2.4 6.3 0 9" fill="none" stroke="#e8605f" stroke-width=".8"/></svg>
          www.LittleWrenNook.example
        </li>
      </ul>
    </div>

    <div class="social">
      <span class="social-slot" role="img" aria-label="Social profile link"></span>
      <span class="social-slot" role="img" aria-label="Social profile link"></span>
    </div>

    <div class="rule"></div>
    <div class="tagline-band"></div>
    <p class="tagline">Handmade Baby Creations</p>
  </section>
</body>
</html>
```